Creative Web Design for an ERP (technology) Consulting Business

I need two pages designed for the ERP Project Management Consulting Company I am starting. One page is the home page, the other page is an important inside page.

I've looked at many different templates for sites like this, and they all look the same to me. I am working with PixelGuild designers because I want something unique.

This site will be implemented with Wordpress using the Elementor framework,

About Me ---
I have worked with PixelGuild several times before, and I have tired to do everything I can to ve helpful. In the uploads, you will find PDF's with wireframes outlning the layout of the pages, as well as explanatios for each section. There are Word documents that you can copy into text. The list below explains the files included.

Although the wireframes suggest a layout, please feel free to use your creativity - often, I find that the designs I like the most are designs I have never thought of.

About the Company --
ERP (Enterprise Resource Planning) systems are business computer systems that tie different businesss functions together. These systems are expensive and complicated, and efforts to implement them often fail. The purpose of the company is to increase the chance of success by focusing on the things that need to be right.

I have uploaded several files to help clarify what I am looking for:
• 1a - Home Page Wireframe - PDF
Wireframe for the home page with an explanation of each section.
• 1b - Home Page Text – Word
A Word document so that you can copy the text.
• 2 - Copper Harbor Logo – ZIP
Four different versions of the company logo in Adobe Illustrator, PNG, and JPG formats. Any of the four are acceptable:
1. Logo_1 – Black on Transparent – Same Line ERP
2. Logo_2 – White on Transparent – Same Line ERP
3. Logo_3 – Black on Transparent – Big ERP on Different Line
4. Logo_4 – White on Transparent – Big ERP on Different Line
• 3a - Copper Harbor Page Wireframe – PDF
Wireframe for he Copper Harbor page, with explanations and a detailed breakdown of the top section.
• 3b - Copper Harbor Text – Word
• 4 - Colors and Palettes – PDF
• 5 - Change Management Icon – EPS
• 6 – Site Map
If you wish to see it, the site map provides an idea of the entire site. The two pages circled in red are the ones I need to be designed.

Thank you for your interest in this project!

Target Market(s)

Corporate decision makers, primarily CIOs and CFOs, as well as ERP project managers and influencers.

Industry/Entity Type

Consulting

Number of Pages Required

2 page

Font styles to use
Sans Serif

Requirements
Must have
• Pages that contain the elements explained on the wireframes provided.
Nice to have
• A design that looks and feels unique
Should not have
• A typical, template layour

```html
<!DOCTYPE html>
<html lang="en">
<head>
<meta charset="utf-8">
<title>Copper Harbor ERP Consulting</title>
<link href="https://fonts.googleapis.com/css2?family=Poppins:wght@300;400;500;600&display=swap" rel="stylesheet">
<style>
:root{
  --ink:#1c1f26;
  --muted:#6b6f78;
  --red:#e8483b;
  --navy:#1b2030;
  --navy-deep:#141826;
  --hero-top:#f4f5f7;
  --hero-bottom:#e3e5e9;
  --panel:#eceef1;
  --line:#d9dce1;
  --white:#ffffff;
}
*{margin:0;padding:0;box-sizing:border-box}
html,body{width:674px;height:1200px;overflow:hidden}
body{font-family:"Poppins",Arial,sans-serif;color:var(--ink);background:var(--white);position:relative}

.site-header{height:46px;display:flex;align-items:center;padding:0 18px;background:var(--white);border-bottom:1px solid var(--line)}
.brand{font-weight:600;font-size:14px;letter-spacing:.5px;display:flex;align-items:center;gap:6px}
.brand-dot{width:9px;height:9px;background:var(--ink)}
.main-nav{display:flex;gap:20px;margin-left:auto;font-size:7.5px;font-weight:500;letter-spacing:.6px;color:var(--muted)}
.search-pill{margin-left:26px;width:40px;height:22px;border:1px solid var(--line);border-radius:11px;display:flex;align-items:center;justify-content:center}
.header-cta{margin-left:12px;background:var(--red);color:var(--white);font-size:7px;font-weight:600;letter-spacing:.6px;height:24px;padding:0 14px;border-radius:12px;display:flex;align-items:center}

.hero{position:relative;height:246px;background:linear-gradient(180deg,var(--hero-top),var(--hero-bottom));text-align:center;padding-top:38px}
.hero-eyebrow{color:var(--red);font-size:11px;font-weight:500;letter-spacing:1.2px}
.hero-title{position:relative;z-index:1;font-weight:400;font-size:27px;line-height:33px;margin:8px auto 0;width:500px}
.btn-dark{display:inline-flex;align-items:center;gap:8px;background:var(--ink);color:var(--white);font-size:8px;font-weight:600;letter-spacing:.8px;border-radius:16px}
.hero .btn-dark{margin-top:16px;height:32px;padding:0 22px}
.hero-deco{position:absolute;left:32px;top:178px;width:70px;height:58px;border-radius:40% 50% 45% 40%;background:linear-gradient(135deg,#c9ccd2,#8e939c)}

.team-photo{height:244px;background:linear-gradient(100deg,#3d4656 0%,#8a8f99 35%,#c9c3bb 60%,#5b6270 100%)}

.content-grid{height:450px;display:grid;grid-template-columns:225px 225px 224px}
.col{position:relative;padding:36px 18px 0}
.col-about{border-right:1px solid var(--line)}
.col-pillars{background:var(--panel)}
.section-title{font-size:20px;font-weight:400;line-height:24px}
.body-text{font-size:6.8px;line-height:10.5px;color:var(--muted);margin-top:10px}
.col-about .btn-dark{margin-top:22px;height:26px;padding:0 16px;font-size:7px}
.divider{height:1px;background:var(--line);margin:36px -18px 0}
.sub-title{font-size:19px;line-height:23px;margin-top:36px;font-weight:400}
.pillars-title{font-size:23px;line-height:29px;font-weight:400}
.pillars-sub{font-size:13px;color:var(--muted);margin-top:14px;font-weight:300}
.pillars-photo{position:absolute;left:63px;bottom:0;width:162px;height:198px;background:linear-gradient(160deg,#d8d4cf,#8d8580 55%,#3a3d46)}
.col-services{padding-left:14px}
.service-item{display:flex;gap:8px;margin-top:16px}
.service-icon{flex:none;width:14px;height:14px}
.service-name{font-size:7.5px;font-weight:500}
.service-desc{font-size:6.3px;line-height:9.5px;color:var(--muted);margin-top:3px}
.experience{margin-top:46px}
.exp-photos{display:flex;gap:4px;margin-top:12px}
.exp-photo{width:100px;height:134px}
.exp-photo.a{background:linear-gradient(160deg,#cfd2d6,#6f747d)}
.exp-photo.b{background:linear-gradient(160deg,#d9cdc2,#5d5f68)}

.site-footer{height:214px;background:var(--navy);color:#c7cad3;position:relative}
.footer-cols{display:grid;grid-template-columns:207px 130px 140px 1fr;padding:34px 18px 0}
.footer-head{font-size:10px;color:var(--white);font-weight:500;margin-bottom:10px}
.footer-text{font-size:6.3px;line-height:9.5px}
.footer-list{list-style:none;font-size:6.3px;line-height:10.5px}
.subscribe{display:flex;margin-top:16px;width:170px;height:22px}
.subscribe-input{flex:1;background:var(--white);border-radius:11px 0 0 11px;font-size:6px;color:var(--muted);display:flex;align-items:center;padding-left:10px}
.subscribe-btn{background:var(--red);color:var(--white);font-size:6.5px;font-weight:600;padding:0 12px;border-radius:0 11px 11px 0;display:flex;align-items:center}
.social{display:flex;gap:8px;margin-bottom:10px}
.social span{width:16px;height:16px;border-radius:50%;background:#c7cad3}
.footer-bottom{position:absolute;left:0;right:0;bottom:0;height:32px;background:var(--navy-deep);display:flex;align-items:center;justify-content:space-between;padding:0 18px;font-size:6px;color:#9ea3ae}
</style>
</head>
<body>
<header class="site-header">
  <div class="brand"><span class="brand-dot"></span>Copper Harbor</div>
  <nav class="main-nav"><span>HOME</span><span>SERVICES</span><span>ERP</span><span>PROJECTS</span><span>CONTACT</span></nav>
  <div class="search-pill"><svg width="10" height="10" viewBox="0 0 10 10"><circle cx="4.2" cy="4.2" r="3" fill="none" stroke="#1c1f26" stroke-width="1.1"/><line x1="6.4" y1="6.4" x2="9" y2="9" stroke="#1c1f26" stroke-width="1.1"/></svg></div>
  <div class="header-cta">TALK TO US</div>
</header>

<section class="hero">
  <div class="hero-deco" role="img" aria-label="Decorative metallic object"></div>
  <p class="hero-eyebrow">INTRODUCTION</p>
  <h1 class="hero-title">Decades in pursuit of excellence in ERP solutions. Let us help you achieve ERP success.</h1>
  <a class="btn-dark">GET STARTED <svg width="8" height="8" viewBox="0 0 8 8"><path d="M4 0v8M0 4h8" stroke="#e8483b" stroke-width="1.6"/></svg></a>
</section>

<div class="team-photo" role="img" aria-label="Photo of a consulting team working together at a table"></div>

<main class="content-grid">
  <section class="col col-about">
    <h2 class="section-title">About Company</h2>
    <p class="body-text">We guide leaders through every stage of ERP change, from early planning and selection to launch and beyond. Our focus stays on the few things that must go right, so projects land on time.</p>
    <a class="btn-dark">LEARN MORE</a>
    <div class="divider"></div>
    <h3 class="sub-title">Root Standard Support Monitor</h3>
    <p class="body-text">Ongoing checks keep your system healthy after launch, with clear reports for finance and IT teams every single month.</p>
  </section>

  <section class="col col-pillars">
    <h2 class="pillars-title">The Copper Harbor Erp Framework &amp; Adaptive 8 Method</h2>
    <p class="pillars-sub">Fundamentals</p>
    <p class="body-text" style="width:120px">Eight proven areas that decide whether an ERP project thrives or stalls.</p>
    <div class="pillars-photo" role="img" aria-label="Photo of two colleagues reviewing documents"></div>
  </section>

  <section class="col col-services">
    <h2 class="section-title">Services</h2>
    <div class="service-item">
      <svg class="service-icon" viewBox="0 0 14 14"><circle cx="7" cy="7" r="6" fill="none" stroke="#e8483b" stroke-width="1.3"/><path d="M4 7l2 2 4-4" fill="none" stroke="#e8483b" stroke-width="1.3"/></svg>
      <div><p class="service-name">Readiness Assessment &amp; Planning</p><p class="service-desc">Clear roadmap built around your goals, people and budget limits.</p></div>
    </div>
    <div class="service-item">
      <svg class="service-icon" viewBox="0 0 14 14"><circle cx="7" cy="7" r="6" fill="none" stroke="#e8483b" stroke-width="1.3"/><path d="M4 7l2 2 4-4" fill="none" stroke="#e8483b" stroke-width="1.3"/></svg>
      <div><p class="service-name">Project Governance Care</p><p class="service-desc">Steady oversight that keeps scope, vendors and teams aligned.</p></div>
    </div>
    <div class="experience">
      <h2 class="section-title">Experience</h2>
      <div class="exp-photos">
        <div class="exp-photo a" role="img" aria-label="Photo of a consultant at work"></div>
        <div class="exp-photo b" role="img" aria-label="Photo of a project meeting"></div>
      </div>
    </div>
  </section>
</main>

<footer class="site-footer">
  <div class="footer-cols">
    <div>
      <p class="footer-head">Subscribe Updates</p>
      <p class="footer-text">Get fresh ERP insights and project tips sent straight to your inbox each month.</p>
      <div class="subscribe"><span class="subscribe-input">Email address</span><span class="subscribe-btn">SUBSCRIBE</span></div>
    </div>
    <div>
      <p class="footer-head">ERP Tools</p>
      <ul class="footer-list"><li>Readiness Check</li><li>Cost Planner</li><li>Risk Review</li><li>Vendor Guide</li><li>Glossary</li></ul>
    </div>
    <div>
      <p class="footer-head">Services</p>
      <ul class="footer-list"><li>Selection Support</li><li>Governance</li><li>Change Management</li><li>Training</li><li>Recovery</li></ul>
    </div>
    <div>
      <p class="footer-head">Service Quality</p>
      <div class="social"><span></span><span></span><span></span><span></span></div>
      <p class="footer-text">Consulting you can trust</p>
    </div>
  </div>
  <div class="footer-bottom"><span>© 2024 Copper Harbor. All rights reserved.</span><span>Privacy · Terms</span></div>
</footer>
</body>
</html>
```